Stationary Design for Quince consultant and support company

We need new stationary designed for a London based support company that provide on-site and remote support services for Quince products. Our clients are both consumers and businesses.

We would like a letterhead, compliment slip, business card and possibly an e-mail signature designed.

Business card designs can be either 1 side or 2, depending on designs we receive we may choose a preference for 1 or 2 sides later on in the design stage.

Designs needs to be at least 300dpi and should be done using CMYK colours.

We want the design to be bold, easy to read, clean and professional.

We have attached our company logo in 2 colour variations (if you need any other source files then please ask).

Our logo colours are as follows:

Blue (85, 50, 0, 0) and Green (50, 0, 100, 0)

We use two different suppliers for out stationary so here are the size dimensions for both. Unfortunately they are ever so slightly different size wise so hopefully we can get something that accommodates both, we can provide dimensions if required for final versions.

Some fonts that have been used before with our company are Probert (for tagline on our company logo) and previously had Nauman used, however we are very much open to seeing what the designers come up with and the fonts mentioned are not a requirement.
Updates

Company details for designs (however the template should be editable for multiple staff) Lumora Ltd. Registered Office: 62-70 Harrowfield Lane London N7 3QD 020 7591 3384 www.lumora-it.example info@lumora-it.example Company is Registered in England and Wales Company No. 07342519 Directors details (if you want to make the template using his details), rest of the details are as above Dan Frost Director dan@lumora-it.example

Hi all, Thank you for your submissions so far. Could we please ask that you don't use the logo with the tagline from our website for the stationary designs and only the logos provided in the design brief. For the business cards we are looking at normal rectangular business cards to be used and we can provide a template guide for size if needed, please just ask. Regards Lumora Team

Target Market(s)

Our target market are consumers (of all ages) and small/medium businesses.

Industry/Entity Type

Business

Font styles to use
Serif
Sans Serif

Requirements
Must have
• At least business card, letterhead and compliment slip submitted (we need all 3 designed this time round)
Should not have
• Business cards should not have the writing "registered office" (letterheads and compliment slips can along the bottom edge)

```html
<!DOCTYPE html>
<html lang="en">
<head>
<meta charset="utf-8">
<title>Lumora Ltd. — Letterhead</title>
<link href="https://fonts.googleapis.com/css2?family=Open+Sans:ital,wght@0,400;0,700;1,400&display=swap" rel="stylesheet">
<style>
  :root {
    --backdrop: #bfe0e7;
    --paper: #ffffff;
    --ink-dark: #2b2b2b;
    --ink-body: #6a6a6a;
    --brand-blue: #2680c2;
    --brand-green: #8cc63f;
    --signature-tone: #ececec;
  }
  * { box-sizing: border-box; margin: 0; padding: 0; }
  html, body {
    width: 1200px; height: 1000px; overflow: hidden;
    background: var(--backdrop);
    font-family: "Open Sans", Arial, sans-serif;
  }
  .letterhead {
    position: absolute; left: 290px; top: 62px;
    width: 620px; height: 877px;
    background: var(--paper);
    box-shadow: 0 2px 8px rgba(0,0,0,0.12);
  }
  .brand-mark {
    position: absolute; left: 48px; top: 52px;
    display: flex; align-items: center; gap: 8px;
  }
  .brand-mark__square { width: 14px; height: 14px; background: var(--brand-blue); }
  .brand-mark__name {
    font-weight: 700; font-size: 32px; letter-spacing: 1px;
    color: var(--ink-dark); line-height: 1;
  }
  .letter-body {
    position: absolute; left: 190px; top: 128px; width: 380px;
    font-size: 9.6px; line-height: 1.62; color: var(--ink-body);
  }
  .letter-body__salutation {
    font-style: italic; font-size: 12px; margin-bottom: 14px; color: #555;
  }
  .letter-body p { margin-bottom: 26px; text-align: justify; }
  .letter-close {
    position: absolute; right: 50px; top: 590px; width: 180px; text-align: right;
  }
  .letter-close__phrase { font-style: italic; font-size: 12px; color: #555; }
  .letter-close__signature {
    display: block; margin: 24px 0 0 auto; width: 150px; height: 52px;
    background: var(--signature-tone);
  }
  .company-footer {
    position: absolute; left: 40px; bottom: 40px;
    display: flex; align-items: flex-start; gap: 10px;
  }
  .company-footer__brand {
    font-weight: 700; font-size: 14px; color: var(--ink-dark); line-height: 1;
  }
  .company-footer__details { font-size: 7.5px; line-height: 1.6; color: var(--ink-body); }
  .company-footer__label { color: var(--brand-green); font-weight: 700; }
  .contact-line { display: flex; align-items: center; gap: 4px; }
  .contact-line svg { width: 7px; height: 7px; fill: var(--brand-blue); flex: none; }
</style>
</head>
<body>
  <main class="letterhead">
    <header class="brand-mark">
      <span class="brand-mark__name">Lumora</span>
      <span class="brand-mark__square"></span>
    </header>

    <section class="letter-body">
      <div class="letter-body__salutation">Dear Client,</div>
      <p>Thank you for choosing us to look after your devices and systems. Our engineers provide on-site and remote support for homes and businesses across London, with clear advice and fast response times. We plan every visit around your schedule, keep you informed at each step, and make sure your equipment is set up, secure and running well before we leave.</p>
      <p>Our support plans cover setup, repairs, data transfer, backups and training. Each plan is tailored to how you work, whether you use a single laptop at home or a network of devices in a growing office. Should anything go wrong, one call to our team is all it takes.</p>
      <p>We have enclosed details of the services discussed during our recent visit, together with a summary of costs. Please review them at your convenience and let us know if you have any questions. We are happy to arrange a follow-up call or a further visit to talk through the options in more detail.</p>
      <p>Thank you again for your trust. We look forward to working with you and keeping your technology running smoothly for years to come.</p>
    </section>

    <section class="letter-close">
      <div class="letter-close__phrase">Best regards,</div>
      <span class="letter-close__signature" role="img" aria-label="Handwritten signature of the sender"></span>
    </section>

    <footer class="company-footer">
      <div class="company-footer__brand">Lumora</div>
      <div class="company-footer__details">
        <div class="company-footer__label">Ltd. Registered</div>
        <div class="contact-line">
          <svg viewBox="0 0 10 10"><path d="M5 0a3.5 3.5 0 0 0-3.5 3.5C1.5 6 5 10 5 10s3.5-4 3.5-6.5A3.5 3.5 0 0 0 5 0zm0 5a1.5 1.5 0 1 1 0-3 1.5 1.5 0 0 1 0 3z"/></svg>
          <span>62-70 Harrowfield Lane</span>
        </div>
        <div class="contact-line"><svg viewBox="0 0 10 10"></svg><span>London N7 3QD</span></div>
        <div class="contact-line">
          <svg viewBox="0 0 10 10"><path d="M2 0.5l2 2-1 1.3c.6 1.3 1.6 2.3 2.9 2.9l1.3-1 2 2L8 9.5C3.9 9.3.7 6.1.5 2z"/></svg>
          <span>020 7591 3384</span>
        </div>
        <div class="contact-line">
          <svg viewBox="0 0 10 10"><path d="M5 0a5 5 0 1 0 0 10A5 5 0 0 0 5 0zm0 1.2c.6.7 1 1.7 1.2 2.8H3.8C4 2.9 4.4 1.9 5 1.2zM3.8 6h2.4C6 7.1 5.6 8.1 5 8.8 4.4 8.1 4 7.1 3.8 6zM1.3 4h1.5v2H1.3a3.8 3.8 0 0 1 0-2zm5.9 0h1.5a3.8 3.8 0 0 1 0 2H7.2z"/></svg>
          <span>www.lumora-it.example</span>
        </div>
        <div class="contact-line">
          <svg viewBox="0 0 10 10"><path d="M0 2h10v6H0zm1 1v.3l4 2.4 4-2.4V3z"/></svg>
          <span>info@lumora-it.example</span>
        </div>
      </div>
    </footer>
  </main>
</body>
</html>
```